vorne matcha

I'm a local business called 'VORNE' and will be sourcing organic ceremonial grade matcha tea through a private labeler in Japan. I need a sleek layout for the label that wraps around the tin that holds the 30g of matcha. I have samples of inspiration and designs that I like. This is very high end matcha so I would like for it to have an expensive look. I also have the dimensions of the label for the tin to show. I have specifics of things that need to be on the label, so please let me know if you need any of that information at this point!

Target Market(s)

High end matcha tea drinkers. The label files I sent are what my eye was drawn to.

Industry/Entity Type

matcha

Font styles to use
Other font styles liked:
• I like the font styles of the samples I uploaded in the photos

Colors

Designer to choose only greyscale colors for use in the design.

Requirements
Must have
• In the biggest lettering of them all in the center is MATCHA. (everything capitalized).Above it, my brand name which is VORNE. and if it looks good, Vorne no.7 like the Duvelle no.5.below the MATCHA, I would like it to say Ceremonial Grade.Another thing... Design wise!I would like the tin to be silver, and the label to be a sort of creme, in between white color with black lettering. Also, I would like the font to be more along the lines of the Ma Verte fonts I sent you... the files that show the cologne bottle with the silver top, creme label, and lettering:)Thanks so much and can't to see what you doOn it as well, the USDA certified organic label, which is in one of the screenshots I uploaded.There needs to be the net weight which is 30g. and also that it is sourced in Uji, Japanmy website on the back: www.saptamatcha.comThe nutrition facts and how to use I will send later:)
Nice to have
• my signature somewhere (like the coffee picture I sent)

```html
<!DOCTYPE html>
<html lang="en">
<head>
<meta charset="utf-8">
<title>Vorne Matcha — Tin Label</title>
<link href="https://fonts.googleapis.com/css2?family=Libre+Caslon+Text:wght@700&family=Space+Mono:wght@400;700&family=Noto+Sans+JP:wght@400&display=swap" rel="stylesheet">
<style>
  :root {
    --page: #ffffff;
    --label: #fefefc;
    --ink: #3b3b3b;
    --ink-soft: #555555;
    --sage: #d7dfcd;
    --leaf: #7f9c5f;
    --shadow: rgba(0,0,0,0.18);
  }
  * { box-sizing: border-box; margin: 0; padding: 0; }
  html, body {
    width: 1200px; height: 1001px; overflow: hidden;
    background: var(--page);
  }
  .stage {
    position: relative; width: 1200px; height: 1001px;
    display: flex; align-items: center; justify-content: center;
  }
  .label {
    position: relative; width: 1120px; height: 208px;
    background: var(--label);
    box-shadow: 0 6px 18px var(--shadow);
    color: var(--ink);
    font-family: "Space Mono", monospace;
    overflow: hidden;
  }

  /* ---------- left panel: facts ---------- */
  .facts {
    position: absolute; left: 70px; top: 24px; width: 238px;
    text-align: center; font-size: 6px; line-height: 1.45;
  }
  .badges {
    display: flex; align-items: center; justify-content: center;
    gap: 8px; margin-top: 6px;
  }
  .origin-box {
    width: 84px; height: 32px; border: 1px solid var(--ink-soft);
    color: var(--leaf); font-size: 6px; line-height: 1.3;
    display: flex; align-items: center; padding-left: 4px; text-align: left;
  }
  .cert-badge {
    width: 30px; height: 30px; border-radius: 50%;
    border: 1.5px solid var(--ink);
  }
  .cert-badge.filled { background: var(--ink); }
  .net { margin-top: 8px; font-weight: 700; font-size: 6.5px; }
  .nutrition {
    margin: 6px auto 0; width: 190px; border-top: 1px solid var(--ink-soft);
    border-bottom: 1px solid var(--ink-soft);
    display: grid; grid-template-columns: 1fr 1fr; text-align: left;
    font-size: 5.5px; padding: 3px 0;
  }

  /* ---------- centre panel: brand ---------- */
  .tagline-jp {
    position: absolute; left: 338px; top: 80px;
    writing-mode: vertical-rl;
    font-family: "Noto Sans JP", sans-serif; font-size: 10px;
    letter-spacing: 0.15em; color: var(--ink);
  }
  .crest-art {
    position: absolute; left: 391px; top: 0; width: 192px; height: 208px;
    background: radial-gradient(ellipse at 50% 50%, var(--sage) 0%, #e6ebe0 60%, rgba(255,255,255,0) 100%);
    opacity: 0.85;
  }
  .brand {
    position: absolute; left: 389px; top: 70px; width: 240px;
    text-align: center;
  }
  .brand .house {
    font-family: "Space Mono", monospace; font-weight: 400;
    font-size: 13px; letter-spacing: 0.3em; color: var(--ink);
  }
  .brand .product {
    font-family: "Libre Caslon Text", serif; font-weight: 700;
    font-size: 40px; line-height: 1; letter-spacing: 0.02em;
    margin-top: 4px;
  }
  .brand .grade {
    font-family: "Space Mono", monospace; font-weight: 700;
    font-size: 14px; letter-spacing: 0.06em; margin-top: 10px;
  }

  /* ---------- right panel: ingredients & use ---------- */
  .info { position: absolute; left: 771px; width: 268px; font-size: 5.6px; line-height: 1.5; }
  .info-box { border: 1px solid var(--ink-soft); padding: 2px 5px 4px; }
  .info-box h3 {
    font-size: 5.6px; font-weight: 700;
    border-bottom: 1px dashed var(--ink-soft); padding-bottom: 1px; margin-bottom: 2px;
  }
  .ingredients { top: 17px; }
  .how-to { top: 54px; height: 111px; }
  .how-to ul { list-style: none; }
  .how-to li { padding-left: 6px; position: relative; text-align: justify; }
  .how-to li::before { content: "›"; position: absolute; left: 0; }
  .claims {
    position: absolute; left: 771px; top: 173px;
    font-size: 7.5px; font-weight: 700; letter-spacing: 0.03em;
  }
  .claims .accent { color: var(--leaf); }
</style>
</head>
<body>
<main class="stage">
  <section class="label">

    <div class="facts">
      <p class="site">www.vornematcha.com</p>
      <p>Certified Organic by NORICERT</p>
      <div class="badges">
        <div class="origin-box">Sourced in<br>Shizuoka,Japan</div>
        <div class="cert-badge filled"></div>
        <div class="cert-badge"></div>
      </div>
      <p class="net">NET WEIGHT: 30G</p>
      <p>Serving Size: 1/2 teaspoon (1g)</p>
      <p>Servings per Container: approximately 30</p>
      <div class="nutrition">
        <span>› Calories: 0g</span><span>› Total Fat: 0g</span>
        <span>› Total Carbohydrates: 0g</span><span>› Sodium: 0g</span>
      </div>
    </div>

    <p class="tagline-jp" lang="ja">生まれ変わった</p>

    <div class="crest-art" role="img" aria-label="Faint sage-green crest illustration behind the product name"></div>

    <div class="brand">
      <p class="house">VORNE</p>
      <h1 class="product">MATCHA</h1>
      <p class="grade">CEREMONIAL GRADE</p>
    </div>

    <div class="info info-box ingredients">
      <h3>INGREDIENTS:</h3>
      <p>Organic Japanese Green Tea Powder</p>
    </div>

    <div class="info info-box how-to">
      <h3>HOW TO USE:</h3>
      <ul>
        <li>Using a chashaku (bamboo tea scoop), measure 2 scoops (1/2 tsp) into a chawan (tea bowl).</li>
        <li>Add 1/4 cup of simmering water (175 degrees) to chawan.</li>
        <li>Using a chasen (bamboo tea whisk), whisk the matcha and hot water. Hold the chasen vertically and barely touching the bottom of the bowl. Stir slowly until matcha is dissolved. Then briskly whisk back and forth in the middle of the tea bowl until a light foam has developed.</li>
        <li>Send love, give gratitude, and enjoy&lt;3</li>
      </ul>
    </div>

    <p class="claims"><span class="accent">VEGAN</span> | GLUTEN FREE | NON GMO</p>

  </section>
</main>
</body>
</html>
```